Delivery Performance Dashboard for Web Portal

We need you to design a dashboard for our web portal. We deliver sand and stone to construction jobsites. The attached screenshot is from our current web portal dashboard . It shows how much material has been delivered from an order.

Loadline will deliver multiple loads during the day and the dispatcher uses the dashboard to monitor if they need to add more trucks or less trucks to fulfill the order. An example would be, I need to ship 1,000 tons of sand to a jobsite and I plan to use 10 trucks during the day and that it will take 10 hours of hauling to complete the job. After 5 hours of hauling (50% the day is over), I should have delivered 500 tons of sand (50% of the order). But maybe there is a lot of traffic, and I only have delivered 300 tons. The dashboard will show that I am behind schedule and I might need to add 2 more trucks to the job.

Industry/Entity Type

Construction

Font styles to use
Sans Serif

Requirements
Must have
• We need a progress bar showing how much material has been delivered, how much material was requested to be delivered total and how much material should have been delivered at the current time. The goal is to show the user if the deliveries are ahead or behind the expected pace and why.
Nice to have
• The icons for plant, driving and jobsite show if the actual times have exceeded or beaten the planned times. Maybe you have other ideas to show the user if the trucks are sitting longer on the jobsite, at the plant to get loaded or driving to and from the jobsite.

```html
<!DOCTYPE html>
<html lang="en">
<head>
<meta charset="utf-8">
<title>Loadline – Delivery Dashboard</title>
<link rel="stylesheet" href="https://fonts.googleapis.com/css2?family=Montserrat:wght@500;600;700&family=Roboto:wght@400;500;700&display=swap">
<style>
:root{
  --stage:#6d6d6d;
  --frame:#e3ebf7;
  --white:#ffffff;
  --blue:#2f86ea;
  --blue-deep:#0a2fcf;
  --navy:#0c2e78;
  --ink:#13306e;
  --text:#3b3f4a;
  --muted:#6e7480;
  --line:#d6dde8;
  --green:#3aa12a;
  --red:#d9261c;
}
*{box-sizing:border-box;margin:0;padding:0}
html,body{width:1053px;height:1200px;overflow:hidden;background:var(--stage);font-family:'Roboto',sans-serif}
.screen{position:absolute;left:63px;width:927px;height:541px;background:var(--frame)}
.screen--one{top:23px}
.screen--two{top:596px}
.sidebar{position:absolute;left:9px;top:13px;width:110px;height:489px;border-radius:20px 0 0 20px;background:linear-gradient(180deg,var(--blue) 0%,#1c5fe0 45%,var(--blue-deep) 100%)}
.brand{position:absolute;left:16px;top:26px;color:var(--white);font-family:'Roboto',sans-serif;font-weight:500;font-size:14px;line-height:16px;letter-spacing:.3px}
.main{position:absolute;left:100px;top:13px;width:811px;height:489px;background:var(--white);border-radius:26px}
.nav{position:absolute;left:0;top:68px;width:100px}
.nav-item{display:flex;align-items:center;height:23px;padding-left:13px;color:var(--white);font-family:'Montserrat',sans-serif;font-weight:500;font-size:7.4px;border-bottom:1px solid rgba(255,255,255,.14)}
.nav-item svg{width:12px;height:12px;margin-right:8px}
.nav-item--active{background:var(--white);color:var(--blue-deep);border-radius:12px 0 0 12px;margin-left:5px;padding-left:9px;border-bottom:none}
.search{position:absolute;left:31px;top:17px;width:216px;height:26px;border:1px solid #b9c3d3;border-radius:13px;padding-left:13px;display:flex;align-items:center;font-size:6.8px;color:var(--muted)}
.search svg{position:absolute;right:11px;top:7px;width:11px;height:11px}
.topbar-link{position:absolute;top:24px;display:flex;align-items:center;font-size:7px;font-weight:500;color:var(--text);letter-spacing:.2px}
.topbar-link svg{width:9px;height:9px;margin-right:3px}
.user{position:absolute;left:726px;top:16px;display:flex;align-items:center}
.avatar{width:21px;height:21px;border-radius:50%;background:radial-gradient(circle at 50% 40%,#8a6b55,#3d3029)}
.user-text{margin-left:5px}
.user-text small{display:block;font-size:5.4px;color:var(--blue)}
.user-text span{display:block;font-size:7.8px;color:var(--text)}
.header-rule{position:absolute;left:0;right:0;top:54px;height:1px;background:var(--line)}
.card{position:absolute;background:var(--white);box-shadow:0 1px 4px rgba(20,40,90,.22);--pad:21px;--col2:139px}
.card--active{background:linear-gradient(180deg,#2f86ea 0%,#1c5ede 100%);box-shadow:0 4px 10px rgba(10,40,140,.3);border-radius:3px;--pad:26px;--col2:145px}
.order-pill{position:absolute;top:-13px;left:50%;transform:translateX(-50%);width:110px;height:32px;border-radius:16px;background:var(--navy);color:var(--white);font-family:'Montserrat',sans-serif;font-size:11px;display:flex;align-items:center;justify-content:center;white-space:nowrap}
.order-pill b{font-weight:700;margin-left:3px}
.origin{position:absolute;left:0;right:0;top:31px;text-align:center;color:var(--ink)}
.origin small{display:block;font-size:9.4px;letter-spacing:.2px}
.origin strong{display:block;font-size:12.2px;font-weight:500;margin-top:1px}
.field{position:absolute;color:var(--ink)}
.field h4{font-weight:400;font-size:8.6px;letter-spacing:.2px}
.field p{font-size:6.8px;color:var(--text);margin-top:4px;line-height:7.6px}
.field p.pos{color:var(--green);font-weight:700;font-size:7.6px;margin-top:8px}
.field p.neg{color:var(--red);font-weight:700;font-size:7.6px;margin-top:8px}
.c1{left:var(--pad)}
.c2{left:var(--col2)}
.card--active .field,.card--active .origin,.card--active .field p{color:var(--white)}
.card--active .field p.pos{color:var(--white)}
.card--active .field p.neg{color:var(--red)}
.waits{display:flex;align-items:center;margin-top:3px}
.waits svg.ic{width:15px;height:15px}
.waits svg.tri{width:4px;height:4px;margin:0 4px 0 1px}
.delta{display:flex;align-items:center;font-size:7px;font-weight:700}
.delta svg{width:12px;height:9px;margin-left:2px}
.tons-bar{position:absolute;left:calc(var(--pad) + 1px);right:12px;height:11px;border-radius:6px;background:linear-gradient(90deg,#2c7ee6,#1f63de);padding:3px 5px}
.card--active .tons-bar{background:rgba(255,255,255,.22)}
.tons-fill{height:5px;border-radius:3px;background:var(--white)}
.tons-meta{position:absolute;left:calc(var(--pad) + 3px);font-size:6.2px;color:var(--blue)}
.tons-meta span+span{margin-left:10px}
.card--active .tons-meta{color:var(--white)}
.pager{position:absolute;left:422px;top:455px;display:flex;align-items:center;font-size:8.6px;color:#333}
.pager svg{width:14px;height:14px}
.pager span{margin:0 5px}
.footer{position:absolute;left:0;right:0;top:514px;text-align:center;font-size:8.3px;color:#444}
.popover{position:absolute;left:117px;top:267px;width:136px;height:171px;background:var(--white);border:1px solid #c7cfdc;box-shadow:0 3px 8px rgba(0,0,0,.18);z-index:5}
.popover::before{content:"";position:absolute;left:62px;top:-6px;border:6px solid transparent;border-top:0;border-bottom-color:var(--navy)}
.popover-head{height:21px;background:var(--navy);color:var(--white);font-size:6.6px;display:flex;align-items:center;padding-left:11px}
.popover-cycle{height:19px;background:#eef1f6;display:flex;align-items:center;justify-content:space-between;padding:0 6px 0 12px;font-size:5.3px;color:var(--muted)}
.popover-cycle svg{width:10px;height:7px}
.popover-row{position:relative;height:32px;border-bottom:1px solid var(--line);font-size:5.5px;color:var(--text)}
.popover-row:last-child{border-bottom:none}
.popover-row svg{position:absolute;left:11px;top:7px;width:18px;height:18px}
.popover-row .what{position:absolute;left:35px;top:9px;line-height:7.5px}
.popover-row .actual{position:absolute;left:94px;top:10px}
</style>
</head>
<body>

<svg width="0" height="0" style="position:absolute" aria-hidden="true">
  <defs>
    <symbol id="ico-plant" viewBox="0 0 20 20"><circle cx="10" cy="10" r="9" fill="#fff" stroke="#1d62dc" stroke-width="1.3"/><path d="M5 14V8l3 2V8l3 2V6h2v2h1v6z" fill="none" stroke="#1d62dc" stroke-width="1"/></symbol>
    <symbol id="ico-truck" viewBox="0 0 20 20"><circle cx="10" cy="10" r="9" fill="#fff" stroke="#1d62dc" stroke-width="1.3"/><path d="M4.5 7h7v5h-7zM11.5 9h2.5l1.5 2v1h-4z" fill="#1d62dc"/><circle cx="7" cy="13" r="1.2" fill="#1d62dc"/><circle cx="13.5" cy="13" r="1.2" fill="#1d62dc"/></symbol>
    <symbol id="ico-pin" viewBox="0 0 20 20"><circle cx="10" cy="10" r="9" fill="#fff" stroke="#1d62dc" stroke-width="1.3"/><path d="M10 4.5a3.5 3.5 0 0 0-3.5 3.5c0 2.6 3.5 6.5 3.5 6.5s3.5-3.9 3.5-6.5A3.5 3.5 0 0 0 10 4.5z" fill="#1d62dc"/><circle cx="10" cy="8" r="1.3" fill="#fff"/></symbol>
    <symbol id="ico-equip" viewBox="0 0 20 20"><circle cx="10" cy="10" r="9" fill="#fff" stroke="#1d62dc" stroke-width="1.3"/><path d="M5 12h9v1.5H5zM7 8h4l1 4H6z" fill="#1d62dc"/><circle cx="7" cy="14" r="1" fill="#1d62dc"/><circle cx="12" cy="14" r="1" fill="#1d62dc"/></symbol>
    <symbol id="tri-up" viewBox="0 0 4 4"><path d="M0 4L2 0l2 4z" fill="#e0302a"/></symbol>
    <symbol id="tri-down" viewBox="0 0 4 4"><path d="M0 0h4L2 4z" fill="#4cbb3a"/></symbol>
    <symbol id="mini-truck" viewBox="0 0 12 9"><path d="M0 1h7v5H0zM7 3h3l2 2v1H7z" fill="currentColor"/><circle cx="2.5" cy="7.2" r="1.3" fill="currentColor"/><circle cx="9.5" cy="7.2" r="1.3" fill="currentColor"/></symbol>
    <symbol id="nav-dash" viewBox="0 0 12 12"><path d="M1.5 9a4.5 4.5 0 1 1 9 0z" fill="none" stroke="currentColor" stroke-width="1"/><path d="M6 9l2-3" stroke="currentColor" stroke-width="1"/></symbol>
    <symbol id="nav-cards" viewBox="0 0 12 12"><rect x="1" y="3" width="10" height="7" rx="1" fill="none" stroke="currentColor" stroke-width=".9"/><path d="M1 5h10" stroke="currentColor" stroke-width=".9"/></symbol>
    <symbol id="nav-account" viewBox="0 0 12 12"><circle cx="6" cy="4" r="2.3" fill="none" stroke="currentColor" stroke-width=".9"/><path d="M2 11c0-2.5 1.8-4 4-4s4 1.5 4 4z" fill="none" stroke="currentColor" stroke-width=".9"/></symbol>
    <symbol id="nav-reports" viewBox="0 0 12 12"><rect x="1" y="2" width="10" height="7.5" fill="none" stroke="currentColor" stroke-width=".9"/><path d="M3.5 8V6M5.5 8V4.5M7.5 8V5.5M4 11h4" stroke="currentColor" stroke-width=".9"/></symbol>
    <symbol id="nav-news" viewBox="0 0 12 12"><rect x="1" y="2" width="10" height="9" fill="none" stroke="currentColor" stroke-width=".9"/><path d="M1 4.5h10M3 6.5h1M5.5 6.5h1M8 6.5h1M3 8.5h1M5.5 8.5h1M8 8.5h1" stroke="currentColor" stroke-width=".9"/></symbol>
    <symbol id="ico-search" viewBox="0 0 12 12"><circle cx="5" cy="5" r="3.6" fill="none" stroke="#1d62dc" stroke-width="1.5"/><path d="M7.7 7.7l3 3" stroke="#1d62dc" stroke-width="1.6" stroke-linecap="round"/></symbol>
    <symbol id="ico-gear" viewBox="0 0 10 10"><circle cx="5" cy="5" r="3.4" fill="none" stroke="#1d62dc" stroke-width="2" stroke-dasharray="1.6 1"/><circle cx="5" cy="5" r="2.6" fill="#1d62dc"/><circle cx="5" cy="5" r="1.1" fill="#fff"/></symbol>
    <symbol id="ico-bell" viewBox="0 0 10 10"><path d="M5 1a3 3 0 0 0-3 3v2.5L1 8h8L8 6.5V4a3 3 0 0 0-3-3z" fill="#1d62dc"/><circle cx="5" cy="9" r="1" fill="#1d62dc"/></symbol>
    <symbol id="pg-prev" viewBox="0 0 14 14"><circle cx="7" cy="7" r="7" fill="#1d62dc"/><path d="M8 4L5 7l3 3" fill="none" stroke="#fff" stroke-width="1.3"/></symbol>
    <symbol id="pg-next" viewBox="0 0 14 14"><circle cx="7" cy="7" r="7" fill="#1d62dc"/><path d="M6 4l3 3-3 3" fill="none" stroke="#fff" stroke-width="1.3"/></symbol>
    <symbol id="ico-swap" viewBox="0 0 10 7"><path d="M1 2h8M7 0.5L9 2 7 3.5M9 5H1M3 3.5L1 5l2 1.5" fill="none" stroke="#1d62dc" stroke-width=".8"/></symbol>
  </defs>
</svg>

<!-- Screen: dashboard overview -->
<section class="screen screen--one">
  <aside class="sidebar">
    <div class="brand">Loadline</div>
    <nav class="nav">
      <div class="nav-item nav-item--active"><svg><use href="#nav-dash"/></svg>Dashboard</div>
      <div class="nav-item"><svg><use href="#nav-cards"/></svg>Cards</div>
      <div class="nav-item"><svg><use href="#nav-account"/></svg>Account</div>
      <div class="nav-item"><svg><use href="#nav-reports"/></svg>Reports</div>
      <div class="nav-item"><svg><use href="#nav-news"/></svg>News</div>
    </nav>
  </aside>
  <main class="main">
    <div class="search">Enter Keyword<svg><use href="#ico-search"/></svg></div>
    <div class="topbar-link" style="left:581px"><svg><use href="#ico-gear"/></svg>SETTINGS</div>
    <div class="topbar-link" style="left:651px"><svg><use href="#ico-bell"/></svg>NOTIFICATION</div>
    <div class="user"><div class="avatar" role="img" aria-label="User profile photo"></div><div class="user-text"><small>Welcome,</small><span>Daniel</span></div></div>
    <div class="header-rule"></div>

    <article class="card card--active" style="left:26px;top:103px;width:234px;height:271px">
      <div class="order-pill">ORDER<b>177746</b></div>
      <div class="origin"><small>ORIGIN</small><strong>Ridgeway Asphalt Plant</strong></div>
      <div class="field c1" style="top:82px"><h4>DESTINATION</h4><p>BZJV 185 from mm 77-98</p></div>
      <div class="field c2" style="top:82px"><h4>CUSTOMER</h4><p>Marlow Construction<br>North Division</p></div>
      <div class="field c1" style="top:122px"><h4>STATUS</h4><p>Accepted</p></div>
      <div class="field c2" style="top:122px"><h4>WAIT TIMES</h4>
        <div class="waits"><svg class="ic"><use href="#ico-plant"/></svg><svg class="tri"><use href="#tri-up"/></svg><svg class="ic"><use href="#ico-truck"/></svg><svg class="tri"><use href="#tri-up"/></svg><svg class="ic"><use href="#ico-pin"/></svg><svg class="tri"><use href="#tri-down"/></svg></div>
      </div>
      <div class="field c1" style="top:169px"><h4>REMAINING</h4><p class="pos">+1.25 hrs</p></div>
      <div class="field c2" style="top:170px"><div class="delta">+/-<svg><use href="#mini-truck"/></svg></div><p class="neg">-31</p></div>
      <div class="field c1" style="top:207px"><h4>TONS</h4></div>
      <div class="tons-bar" style="top:222px"><div class="tons-fill" style="width:52%"></div></div>
      <div class="tons-meta" style="top:238px"><span>722.57/1500</span><span>7:30 am - 5:00 pm</span></div>
    </article>

    <article class="card" style="left:279px;top:105px;width:224px;height:263px">
      <div class="order-pill">ORDER<b>177746</b></div>
      <div class="origin"><small>ORIGIN</small><strong>Cedar Hill Asphalt Plant</strong></div>
      <div class="field c1" style="top:82px"><h4>DESTINATION</h4><p>Pine Hollow</p></div>
      <div class="field c2" style="top:82px"><h4>CUSTOMER</h4><p>Marlow Construction<br>North Division</p></div>
      <div class="field c1" style="top:122px"><h4>STATUS</h4><p>Accepted</p></div>
      <div class="field c2" style="top:122px"><h4>WAIT TIMES</h4>
        <div class="waits"><svg class="ic"><use href="#ico-plant"/></svg><svg class="tri"><use href="#tri-up"/></svg><svg class="ic"><use href="#ico-truck"/></svg><svg class="tri"><use href="#tri-up"/></svg><svg class="ic"><use href="#ico-pin"/></svg><svg class="tri"><use href="#tri-down"/></svg></div>
      </div>
      <div class="field c1" style="top:169px"><h4>REMAINING</h4><p class="pos">+1.10 hrs</p></div>
      <div class="field c2" style="top:170px"><div class="delta">+/-<svg style="color:var(--navy)"><use href="#mini-truck"/></svg></div><p class="neg">-31</p></div>
      <div class="field c1" style="top:207px"><h4>TONS</h4></div>
      <div class="tons-bar" style="top:222px"><div class="tons-fill" style="width:34%"></div></div>
      <div class="tons-meta" style="top:238px"><span>722.57/1500</span><span>7:30 am - 5:00 pm</span></div>
    </article>

    <article class="card" style="left:526px;top:107px;width:225px;height:263px">
      <div class="order-pill">ORDER<b>177746</b></div>
      <div class="origin"><small>ORIGIN</small><strong>Ridgeway Asphalt Plant</strong></div>
      <div class="field c1" style="top:82px"><h4>DESTINATION</h4><p>BZJV-185 from mm 77-98</p></div>
      <div class="field c2" style="top:82px"><h4>CUSTOMER</h4><p>Marlow Construction<br>North Division</p></div>
      <div class="field c1" style="top:122px"><h4>STATUS</h4><p>Accepted</p></div>
      <div class="field c2" style="top:122px"><h4>WAIT TIMES</h4>
        <div class="waits"><svg class="ic"><use href="#ico-plant"/></svg><svg class="tri"><use href="#tri-up"/></svg><svg class="ic"><use href="#ico-truck"/></svg><svg class="tri"><use href="#tri-up"/></svg><svg class="ic"><use href="#ico-pin"/></svg><svg class="tri"><use href="#tri-down"/></svg></div>
      </div>
      <div class="field c1" style="top:169px"><h4>REMAINING</h4><p class="pos">+1.25 hrs</p></div>
      <div class="field c2" style="top:170px"><div class="delta">+/-<svg style="color:var(--navy)"><use href="#mini-truck"/></svg></div><p class="neg">-25</p></div>
      <div class="field c1" style="top:207px"><h4>TONS</h4></div>
      <div class="tons-bar" style="top:222px"><div class="tons-fill" style="width:18%"></div></div>
      <div class="tons-meta" style="top:238px"><span>722.57/1500</span><span>7:30 am - 5:00 pm</span></div>
    </article>

    <div class="pager"><svg><use href="#pg-prev"/></svg><span>1-3 &nbsp;of &nbsp;3</span><svg><use href="#pg-next"/></svg></div>
  </main>
  <p class="footer">© 2020 Company Name | All Rights Reserved</p>
</section>

<!-- Screen: wait time detail open -->
<section class="screen screen--two">
  <aside class="sidebar">
    <div class="brand">Loadline</div>
    <nav class="nav">
      <div class="nav-item nav-item--active"><svg><use href="#nav-dash"/></svg>Dashboard</div>
      <div class="nav-item"><svg><use href="#nav-cards"/></svg>Cards</div>
      <div class="nav-item"><svg><use href="#nav-account"/></svg>Account</div>
      <div class="nav-item"><svg><use href="#nav-reports"/></svg>Reports</div>
      <div class="nav-item"><svg><use href="#nav-news"/></svg>News</div>
    </nav>
  </aside>
  <main class="main">
    <div class="search">Enter Keyword<svg><use href="#ico-search"/></svg></div>
    <div class="topbar-link" style="left:581px"><svg><use href="#ico-gear"/></svg>SETTINGS</div>
    <div class="topbar-link" style="left:651px"><svg><use href="#ico-bell"/></svg>NOTIFICATION</div>
    <div class="user"><div class="avatar" role="img" aria-label="User profile photo"></div><div class="user-text"><small>Welcome,</small><span>Daniel</span></div></div>
    <div class="header-rule"></div>

    <article class="card card--active" style="left:26px;top:103px;width:234px;height:271px">
      <div class="order-pill">ORDER<b>177746</b></div>
      <div class="origin"><small>ORIGIN</small><strong>Ridgeway Asphalt Plant</strong></div>
      <div class="field c1" style="top:82px"><h4>DESTINATION</h4><p>BZJV 185 from mm 77-98</p></div>
      <div class="field c2" style="top:82px"><h4>CUSTOMER</h4><p>Marlow Construction<br>North Division</p></div>
      <div class="field c1" style="top:122px"><h4>STATUS</h4><p>Accepted</p></div>
      <div class="field c2" style="top:122px"><h4>WAIT TIMES</h4>
        <div class="waits"><svg class="ic"><use href="#ico-plant"/></svg><svg class="tri"><use href="#tri-up"/></svg><svg class="ic"><use href="#ico-truck"/></svg><svg class="tri"><use href="#tri-up"/></svg><svg class="ic"><use href="#ico-pin"/></svg><svg class="tri"><use href="#tri-down"/></svg></div>
      </div>
      <div class="field c1" style="top:169px"><h4>REMAINING</h4><p class="pos">+1.25 hrs</p></div>
      <div class="field c1" style="top:207px"><h4>TONS</h4></div>
      <div class="tons-bar" style="top:222px"><div class="tons-fill" style="width:52%"></div></div>
      <div class="tons-meta" style="top:238px"><span>722.57/1500</span><span>7:30 am - 5:00 pm</span></div>
    </article>

    <article class="card" style="left:279px;top:105px;width:224px;height:263px">
      <div class="order-pill">ORDER<b>177746</b></div>
      <div class="origin"><small>ORIGIN</small><strong>Cedar Hill Asphalt Plant</strong></div>
      <div class="field c1" style="top:82px"><h4>DESTINATION</h4><p>Pine Hollow</p></div>
      <div class="field c2" style="top:82px"><h4>CUSTOMER</h4><p>Marlow Construction<br>North Division</p></div>
      <div class="field c1" style="top:122px"><h4>STATUS</h4><p>Accepted</p></div>
      <div class="field c2" style="top:122px"><h4>WAIT TIMES</h4>
        <div class="waits"><svg class="ic"><use href="#ico-plant"/></svg><svg class="tri"><use href="#tri-up"/></svg><svg class="ic"><use href="#ico-truck"/></svg><svg class="tri"><use href="#tri-up"/></svg><svg class="ic"><use href="#ico-pin"/></svg><svg class="tri"><use href="#tri-down"/></svg></div>
      </div>
      <div class="field c1" style="top:169px"><h4>REMAINING</h4><p class="pos">+1.10 hrs</p></div>
      <div class="field c2" style="top:170px"><div class="delta">+/-<svg style="color:var(--navy)"><use href="#mini-truck"/></svg></div><p class="neg">-31</p></div>
      <div class="field c1" style="top:207px"><h4>TONS</h4></div>
      <div class="tons-bar" style="top:222px"><div class="tons-fill" style="width:34%"></div></div>
      <div class="tons-meta" style="top:238px"><span>722.57/1500</span><span>7:30 am - 5:00 pm</span></div>
    </article>

    <article class="card" style="left:526px;top:107px;width:225px;height:263px">
      <div class="order-pill">ORDER<b>177746</b></div>
      <div class="origin"><small>ORIGIN</small><strong>Ridgeway Asphalt Plant</strong></div>
      <div class="field c1" style="top:82px"><h4>DESTINATION</h4><p>BZJV-185 from mm 77-98</p></div>
      <div class="field c2" style="top:82px"><h4>CUSTOMER</h4><p>Marlow Construction<br>North Division</p></div>
      <div class="field c1" style="top:122px"><h4>STATUS</h4><p>Accepted</p></div>
      <div class="field c2" style="top:122px"><h4>WAIT TIMES</h4>
        <div class="waits"><svg class="ic"><use href="#ico-plant"/></svg><svg class="tri"><use href="#tri-up"/></svg><svg class="ic"><use href="#ico-truck"/></svg><svg class="tri"><use href="#tri-up"/></svg><svg class="ic"><use href="#ico-pin"/></svg><svg class="tri"><use href="#tri-down"/></svg></div>
      </div>
      <div class="field c1" style="top:169px"><h4>REMAINING</h4><p class="pos">+1.25 hrs</p></div>
      <div class="field c2" style="top:170px"><div class="delta">+/-<svg style="color:var(--navy)"><use href="#mini-truck"/></svg></div><p class="neg">-25</p></div>
      <div class="field c1" style="top:207px"><h4>TONS</h4></div>
      <div class="tons-bar" style="top:222px"><div class="tons-fill" style="width:18%"></div></div>
      <div class="tons-meta" style="top:238px"><span>722.57/1500</span><span>7:30 am - 5:00 pm</span></div>
    </article>

    <div class="popover">
      <div class="popover-head">ORDER 17746</div>
      <div class="popover-cycle"><svg><use href="#ico-swap"/></svg><span>Avg Cycle Time: 2hr 27 min</span></div>
      <div class="popover-row"><svg><use href="#ico-plant"/></svg><div class="what">Plant (min)<br>Planned: 30</div><div class="actual">Actual: 33</div></div>
      <div class="popover-row"><svg><use href="#ico-truck"/></svg><div class="what">Driving (min)<br>Planned: 60</div><div class="actual">Actual: 83</div></div>
      <div class="popover-row"><svg><use href="#ico-pin"/></svg><div class="what">Jobsite (min)<br>Planned: 30</div><div class="actual">Actual: 30</div></div>
      <div class="popover-row"><svg><use href="#ico-equip"/></svg><div class="what">Equipment (min)</div><div class="actual" style="left:95px">Actualy:-</div></div>
    </div>

    <div class="pager"><svg><use href="#pg-prev"/></svg><span>1-3 &nbsp;of &nbsp;3</span><svg><use href="#pg-next"/></svg></div>
  </main>
  <p class="footer">© 2020 Company Name | All Rights Reserved</p>
</section>

</body>
</html>
```